Non fiction leadership Book Cover design needed for “Stay Bold: Build On Lasting Discipline”

I need a front cover design for a new book 6 X 9 traditional non-fiction book.

Title: "Stay BOLD - Build On Lasting Discipline"

The subtitle is not finalized- so use 2 lines of smaller dummy text

My brand guide is attached (please use the tan color sparingly)

I'd like to see BOLD look like it is in motion and "flying" across the page

Need CREATIVE designs and options

Do not want my picture on the front cover - I do want it on the back cover.

On the front cover I’d like to see creative use of font to create movement on “BOLD”

Target Market(s)

Business leaders

Industry/Entity Type

Aviation

Font styles to use
Other font styles liked:
• See style guide- can add additional font (modern script or san serif)

Colors
0054AA
0677BA
7BADD7
CADEEF
E8F1F8
EB3D1F
EC4F4E
F09395
F8D3D4
FCEDEE

Requirements
Must have
• Creative font use, using perspective to create movement/motion on BOLD
Should not have
• My picture on the front cover- my picture should be on the back cover

```html
<!DOCTYPE html>
<html lang="en">
<head>
<meta charset="utf-8">
<title>Stay BOLD - Build On Lasting Discipline — Book Cover</title>
<link rel="stylesheet" href="https://fonts.googleapis.com/css2?family=Big+Shoulders+Display:wght@900&family=Montserrat:wght@500;600&display=swap">
<style>
  :root {
    --backdrop: #b1b0ad;
    --navy: #0c1a5c;
    --cream: #f9f2ec;
    --tan-light: #ecd3ae;
    --tan-mid: #cf9f66;
    --tan-deep: #a9621f;
    --white: #ffffff;
  }
  * { margin: 0; padding: 0; box-sizing: border-box; }
  html, body {
    width: 1200px;
    height: 960px;
    overflow: hidden;
    background: var(--backdrop);
  }
  .stage {
    position: relative;
    width: 1200px;
    height: 960px;
  }
  .book-cover {
    position: absolute;
    left: 318px;
    top: 40px;
    width: 563px;
    height: 880px;
    background: var(--cream);
    overflow: hidden;
    box-shadow: 0 10px 30px rgba(0, 0, 0, 0.18);
  }
  .cover-art {
    position: absolute;
    inset: 0;
    width: 563px;
    height: 880px;
  }
  .title-word {
    font-family: "Big Shoulders Display", sans-serif;
    font-weight: 900;
  }
  .teaser {
    position: absolute;
    top: 17px;
    left: 0;
    width: 100%;
    text-align: center;
    font-family: "Montserrat", sans-serif;
    font-weight: 500;
    font-size: 12.5px;
    line-height: 16px;
    color: var(--white);
  }
  .subtitle-bar {
    position: absolute;
    left: 68px;
    top: 744px;
    width: 429px;
    height: 46px;
    background: var(--navy);
    color: var(--white);
    font-family: "Montserrat", sans-serif;
    font-weight: 600;
    font-size: 23px;
    letter-spacing: 0.3px;
    display: flex;
    align-items: center;
    justify-content: center;
    white-space: nowrap;
  }
  .author {
    position: absolute;
    top: 812px;
    left: 0;
    width: 100%;
    text-align: center;
    font-family: "Montserrat", sans-serif;
    font-weight: 600;
    font-size: 33px;
    line-height: 40px;
    color: var(--navy);
  }
</style>
</head>
<body>
<main class="stage">
  <section class="book-cover" aria-label="Book cover: Stay BOLD - Build On Lasting Discipline">
    <svg class="cover-art" viewBox="0 0 563 880" xmlns="http://www.w3.org/2000/svg">
      <defs>
        <linearGradient id="tan-fade" x1="0" y1="0" x2="0" y2="1">
          <stop offset="0" stop-color="#ecd3ae"/>
          <stop offset="0.55" stop-color="#cf9f66"/>
          <stop offset="0.85" stop-color="#bf8450"/>
          <stop offset="1" stop-color="#a9621f"/>
        </linearGradient>
      </defs>

      <rect class="sky-band" x="0" y="0" width="563" height="300" fill="#0c1a5c"/>
      <polygon class="peak" points="0,283 284,213 563,282 563,880 0,880" fill="#f9f2ec"/>

      <rect class="aircraft-mark" x="236" y="82" width="96" height="130" rx="8"
            fill="#f9f2ec" opacity="0.85" role="img"
            aria-label="Helicopter silhouette seen from above, rotor blades crossed"/>

      <text class="title-word title-top" x="285" y="344" text-anchor="middle"
            font-size="111" textLength="176" lengthAdjust="spacingAndGlyphs"
            fill="#0c1a5c">STAY</text>

      <g class="speed-lines" stroke="#0c1a5c" stroke-linecap="round">
        <line x1="14" y1="420" x2="104" y2="420" stroke-width="4"/>
        <line x1="34" y1="470" x2="96" y2="470" stroke-width="3"/>
        <line x1="8" y1="560" x2="86" y2="560" stroke-width="4"/>
        <line x1="30" y1="620" x2="76" y2="620" stroke-width="3"/>
        <line x1="12" y1="690" x2="66" y2="690" stroke-width="4"/>
      </g>

      <g class="title-word title-main" font-size="465"
         transform="translate(250,735) skewX(-12) translate(-250,-735)">
        <text x="238" y="735" text-anchor="middle" textLength="360" lengthAdjust="spacingAndGlyphs" fill="#0c1a5c" opacity="0.35">BOLD</text>
        <text x="244" y="735" text-anchor="middle" textLength="360" lengthAdjust="spacingAndGlyphs" fill="#0c1a5c">BOLD</text>
        <text x="250" y="735" text-anchor="middle" textLength="360" lengthAdjust="spacingAndGlyphs" fill="url(#tan-fade)">BOLD</text>
      </g>
    </svg>

    <p class="teaser">Lorem ipsum dolor sit amet, consectetuer adipiscing<br>sed diam nonummy nibh euismod tincidunt</p>
    <p class="subtitle-bar">BUILD ON LASTING DISCIPLINE</p>
    <p class="author">Margaret Holloway</p>
  </section>
</main>
</body>
</html>
```